Global (re)insurance broker needs a business card design

We need a classic business card for our company that is headquartered in SG, with offices in Malaysia and Dubai. We specialise in insurance and reinsurance broking and consultancy for our global clients.

```html
<!DOCTYPE html>
<html lang="en">
<head>
<meta charset="utf-8">
<title>Norvane Business Card</title>
<link rel="stylesheet" href="https://fonts.googleapis.com/css2?family=Open+Sans:wght@400;600;700&display=swap">
<style>
  :root {
    --page: #2a292e;
    --card: #1e1d22;
    --rim: #c5e0b8;
    --mint: #c5e0b8;
    --blue: #2d4ea3;
    --ink: #f2f2f2;
    --pattern-dark: #17161a;
    --pattern-light: #2c2b31;
  }
  * { box-sizing: border-box; margin: 0; padding: 0; }
  html, body { width: 1200px; height: 780px; overflow: hidden; }
  body {
    background: var(--page);
    font-family: "Open Sans", Arial, sans-serif;
    display: flex;
    align-items: center;
    justify-content: center;
    gap: 40px;
  }
  .card {
    position: relative;
    width: 540px;
    height: 310px;
    background: var(--card);
    border: 3px solid var(--rim);
    border-radius: 26px;
    overflow: hidden;
  }

  /* Back side */
  .card-back .pattern-field {
    position: absolute;
    inset: 0;
    background: linear-gradient(160deg, var(--pattern-light) 0%, var(--pattern-dark) 55%, var(--pattern-light) 100%);
  }
  .card-back .back-wordmark {
    position: absolute;
    right: 70px;
    top: 150px;
    font-size: 18px;
    font-weight: 600;
    letter-spacing: 0.5px;
    color: var(--mint);
  }

  /* Front side */
  .wordmark {
    position: absolute;
    left: 34px;
    top: 58px;
    font-size: 48px;
    font-weight: 700;
    letter-spacing: 0.5px;
    line-height: 1;
    white-space: nowrap;
    color: var(--mint);
  }
  .identity {
    position: absolute;
    right: 40px;
    top: 38px;
    text-align: right;
    white-space: nowrap;
  }
  .identity .name {
    font-size: 26px;
    font-weight: 700;
    line-height: 1.1;
    color: var(--blue);
  }
  .identity .name .surname { color: var(--mint); }
  .identity .role {
    font-size: 12px;
    font-weight: 600;
    color: var(--ink);
  }
  .accent-bar {
    position: absolute;
    right: 0;
    top: 32px;
    width: 24px;
    height: 56px;
    background: var(--mint);
  }
  .address {
    position: absolute;
    left: 38px;
    top: 145px;
    font-size: 14px;
    line-height: 1.45;
    color: var(--ink);
  }
  .contacts {
    position: absolute;
    left: 38px;
    bottom: 26px;
    list-style: none;
  }
  .contacts li {
    display: flex;
    align-items: center;
    gap: 10px;
    font-size: 14px;
    line-height: 22px;
    color: var(--ink);
  }
  .contacts svg { width: 14px; height: 14px; flex: none; }
</style>
</head>
<body>

  <section class="card card-back" aria-label="Card back">
    <div class="pattern-field" role="img" aria-label="Repeating company name pattern in dark grey tones"></div>
    <div class="back-wordmark">NORVANE</div>
  </section>

  <section class="card card-front" aria-label="Card front">
    <div class="wordmark">NORVANE</div>

    <div class="identity">
      <div class="name">Mira <span class="surname">Lowe</span></div>
      <div class="role">Chief Operating Officer</div>
    </div>
    <div class="accent-bar"></div>

    <p class="address">22 Harbour Lane, Meridian<br>Tower #08-04, Singapore 048512</p>

    <ul class="contacts">
      <li>
        <svg viewBox="0 0 14 14" aria-hidden="true"><rect x="3" y="1" width="8" height="12" rx="1.5" fill="none" stroke="var(--mint)" stroke-width="1.4"/></svg>
        +65 9100 2468
      </li>
      <li>
        <svg viewBox="0 0 14 14" aria-hidden="true"><circle cx="7" cy="7" r="6" fill="var(--blue)"/><path d="M1 7h12M7 1c-3 3-3 9 0 12M7 1c3 3 3 9 0 12" fill="none" stroke="var(--card)" stroke-width="0.8"/></svg>
        www.norvane.com
      </li>
      <li>
        <svg viewBox="0 0 14 14" aria-hidden="true"><rect x="1" y="3" width="12" height="9" rx="1" fill="none" stroke="var(--mint)" stroke-width="1.3"/><path d="M1.5 3.5L7 8l5.5-4.5" fill="none" stroke="var(--mint)" stroke-width="1.3"/></svg>
        mira@norvane.com
      </li>
    </ul>
  </section>

</body>
</html>
```